Business Card Design Project

We need a business card for a new technology services company. We develop software and implement software packages for our business customers and although we will begin with just one or two service offerings, our service offerings will expand over time. Our name comes from the an author, KL Barrow, and his "idea" was that opportunity should be based on ability and achievement, not on social status.

We would like to see a design that is standard in its size and shape, but stands apart in its dramatic color contrasts. The card should not use too many colors - the colors used in the background should highlight the brilliant blues of the logo (see attachment) to dramatic effect. The background should not be white.

If necessary, you can change the color of the words "KL Barrow", but not the word "Idea".

Card size should be U.S. standard 2 inches by 3.5 inches and provide for 1/8 inch bleed area on each side.

We need a design for both sides of the business card, one side communicating the company logo and contact information, the other side being purely graphical, incorporating the logo but no other information.

Contact Information Required:
Kate Brook
KateBrook@klbarrowvista.com
614-387-2259

Target Market(s)

Business executives

Industry/Entity Type

Software

Requirements
Must have
• It must have the full company logo on one side, and at least the graphic element of the logo on the other. Either that or the full logo on both.
Nice to have
• It would be nice to have a design that could work without needing two different textures. For example, it would be nice if the entire card could be shiny, not just parts of the card.

It would also be nice if texture is something we could add later.
Should not have
• The card should not use the color green.

```html
<!DOCTYPE html>
<html lang="en">
<head>
<meta charset="utf-8">
<title>Barrow Vista — Business Card</title>
<link href="https://fonts.googleapis.com/css2?family=Roboto:wght@300;400&family=Cinzel:wght@400&display=swap" rel="stylesheet">
<style>
  :root {
    --page-bg: #e7e4df;
    --card-dark: #121212;
    --card-mid: #2c2c2c;
    --brand-blue: #1ba6e6;
    --text-light: #f2f2f2;
    --shadow: rgba(0, 0, 0, 0.35);
  }
  * { box-sizing: border-box; margin: 0; padding: 0; }
  html, body {
    width: 1200px;
    height: 750px;
    overflow: hidden;
    background: var(--page-bg);
  }
  .canvas {
    position: relative;
    width: 1200px;
    height: 750px;
    background: var(--page-bg);
  }
  .card {
    position: absolute;
    width: 540px;
    height: 309px;
    border-radius: 3px;
    overflow: hidden;
    background: radial-gradient(ellipse 70% 80% at 50% 60%, var(--card-mid) 0%, var(--card-dark) 75%);
    box-shadow: 0 12px 28px var(--shadow);
    font-family: "Roboto", "Helvetica Neue", Arial, sans-serif;
  }
  .card--front { left: 40px; top: 60px; }
  .card--back { left: 620px; top: 381px; }

  .wordmark {
    position: absolute;
    display: flex;
    align-items: center;
  }
  .wordmark__name {
    color: var(--brand-blue);
    font-weight: 300;
    letter-spacing: -0.5px;
    white-space: nowrap;
    line-height: 1;
  }
  .wordmark__dot {
    border-radius: 50%;
    background: var(--brand-blue);
    flex: none;
  }
  .card--front .wordmark { left: 50px; top: 58px; }
  .card--front .wordmark__name { font-size: 38px; }
  .card--front .wordmark__dot { width: 110px; height: 110px; margin-left: 90px; }

  .card--back .wordmark { left: 60px; top: 104px; }
  .card--back .wordmark__name { font-size: 44px; }
  .card--back .wordmark__dot { width: 100px; height: 100px; margin-left: 60px; }

  .contact-name {
    position: absolute;
    left: 50px;
    top: 188px;
    font-family: "Cinzel", "Times New Roman", serif;
    font-size: 19px;
    letter-spacing: 1px;
    color: var(--brand-blue);
    text-decoration: underline;
    text-underline-offset: 3px;
  }
  .contact-list {
    position: absolute;
    left: 50px;
    top: 228px;
    list-style: none;
  }
  .contact-list__item {
    display: flex;
    align-items: center;
    gap: 8px;
    font-size: 14px;
    color: var(--text-light);
    line-height: 26px;
  }
  .contact-list__icon { width: 11px; height: 11px; flex: none; }
</style>
</head>
<body>
<main class="canvas">

  <section class="card card--front" aria-label="Business card front">
    <div class="wordmark">
      <span class="wordmark__name">Barrow Vista</span>
      <span class="wordmark__dot" aria-hidden="true"></span>
    </div>
    <p class="contact-name">Kate Brook</p>
    <ul class="contact-list">
      <li class="contact-list__item">
        <svg class="contact-list__icon" viewBox="0 0 12 12" aria-hidden="true">
          <path d="M2.5 1 L4.5 1 L5.2 3.6 L3.9 4.6 C4.6 6 5.9 7.4 7.4 8.1 L8.4 6.8 L11 7.5 L11 9.5 C11 10.4 10.3 11 9.5 11 C5 10.6 1.4 7 1 2.5 C1 1.7 1.6 1 2.5 1 Z" fill="var(--brand-blue)"/>
        </svg>
        614-387-2259
      </li>
      <li class="contact-list__item">
        <svg class="contact-list__icon" viewBox="0 0 12 12" aria-hidden="true">
          <rect x="0.5" y="2.5" width="11" height="7.5" rx="1" fill="var(--brand-blue)"/>
          <path d="M1 3 L6 7 L11 3" fill="none" stroke="var(--card-dark)" stroke-width="1"/>
        </svg>
        KateBrook@klbarrowvista.com
      </li>
    </ul>
  </section>

  <section class="card card--back" aria-label="Business card back">
    <div class="wordmark">
      <span class="wordmark__name">Barrow Vista</span>
      <span class="wordmark__dot" aria-hidden="true"></span>
    </div>
  </section>

</main>
</body>
</html>
```